Design logo, business cards, and web page for new web and bi development consulting company

I've started a Web and Business Intelligence development consulting company. We develop on Quordex's stack, Visual Sudio and SQL Server. We develop responsive web sites and business intelligence platforms. I plan on focusing on small to medium sized business as my client base. I need a logo, business cards, and a one page web site. We will do more with the web site with you in the next six months if the business survives. The name of the company is Corvalo Integration Solutions, Corvalo for short.

Target Market(s)

small to medium sized businesses

Industry/Entity Type

Business

Contact Information for Business Card

logo
name
title
email
phone

Logo Text

Corvalo Integration Solutions - web and data solutions

Coding

Coded - Design and coding required

Number of Pages Required

1 page

Font styles to use
Sans Serif

Colors
0355a3
0092cd
00a88f
6b449b

Requirements
Nice to have
• web and data solutions

```html
<!DOCTYPE html>
<html lang="en">
<head>
<meta charset="utf-8">
<title>Corvalo Integration Solutions</title>
<link href="https://fonts.googleapis.com/css2?family=Open+Sans:wght@300;400;600&display=swap" rel="stylesheet">
<style>
  :root {
    --night: #05070d;
    --deep-navy: #0a1428;
    --glow-blue: #1f5fb8;
    --sky: #0092cd;
    --brand-blue: #0355a3;
    --button-blue: #1976d2;
    --white: #ffffff;
    --soft-white: rgba(255, 255, 255, 0.82);
  }
  * { margin: 0; padding: 0; box-sizing: border-box; }
  html, body {
    width: 1200px;
    height: 800px;
    overflow: hidden;
    background: var(--night);
    font-family: "Open Sans", Arial, sans-serif;
    color: var(--white);
  }
  .hero {
    position: relative;
    width: 1200px;
    height: 800px;
    overflow: hidden;
  }
  .hero-visual {
    position: absolute;
    inset: 0;
    background:
      radial-gradient(circle at 350px 420px, rgba(120, 170, 240, 0.75) 0, rgba(40, 100, 190, 0.45) 110px, rgba(10, 30, 70, 0) 300px),
      radial-gradient(ellipse at 600px 400px, rgba(40, 80, 150, 0.45) 0, rgba(10, 20, 45, 0) 420px),
      linear-gradient(115deg, var(--night) 0%, var(--deep-navy) 45%, #0d1a33 65%, var(--night) 100%);
  }
  .hero-sheen {
    position: absolute;
    top: 0;
    right: 0;
    width: 560px;
    height: 800px;
    background: linear-gradient(200deg, rgba(255, 255, 255, 0.07) 0%, rgba(255, 255, 255, 0) 60%);
    clip-path: polygon(38% 0, 100% 0, 100% 100%, 0 100%);
  }
  .site-header {
    position: absolute;
    top: 36px;
    left: 120px;
    right: 150px;
    display: flex;
    justify-content: space-between;
    align-items: flex-start;
  }
  .brand { display: flex; flex-direction: column; gap: 4px; }
  .brand-name { font-size: 34px; font-weight: 400; line-height: 1; }
  .brand-tagline { font-size: 17px; font-weight: 400; }
  .main-nav { display: flex; gap: 30px; margin-top: 26px; }
  .main-nav a {
    color: var(--white);
    text-decoration: none;
    font-size: 13px;
    letter-spacing: 0.3px;
  }
  .hero-copy {
    position: absolute;
    right: 124px;
    top: 300px;
    width: 560px;
    text-align: right;
  }
  .hero-title {
    font-weight: 300;
    font-size: 48px;
    line-height: 56px;
    letter-spacing: -0.5px;
  }
  .hero-text {
    margin-top: 20px;
    font-size: 11.5px;
    line-height: 16px;
    color: var(--soft-white);
  }
  .hero-actions {
    position: absolute;
    left: 810px;
    top: 504px;
    display: flex;
    align-items: flex-start;
    gap: 8px;
  }
  .btn {
    display: inline-flex;
    align-items: center;
    justify-content: center;
    font-size: 14px;
    color: var(--white);
    text-decoration: none;
    border-radius: 4px;
  }
  .btn-outline {
    width: 145px;
    height: 68px;
    margin-top: 10px;
    border: 1.5px solid var(--white);
  }
  .btn-primary {
    width: 137px;
    height: 66px;
    background: var(--button-blue);
  }
  .slider-arrow {
    position: absolute;
    width: 46px;
    height: 48px;
    background: var(--button-blue);
    display: flex;
    align-items: center;
    justify-content: center;
  }
  .slider-prev { left: 62px; top: 432px; }
  .slider-next { left: 1118px; top: 364px; width: 40px; height: 46px; }
</style>
</head>
<body>
  <main class="hero">
    <div class="hero-visual" role="img" aria-label="Background photograph of a person holding a glowing globe surrounded by floating data charts, in deep blue tones"></div>
    <div class="hero-sheen"></div>

    <header class="site-header">
      <div class="brand">
        <span class="brand-name">Corvalo</span>
        <span class="brand-tagline">Integration Solutions</span>
      </div>
      <nav class="main-nav">
        <a href="#">HOME</a>
        <a href="#">ABOUT</a>
        <a href="#">OUR TEAM</a>
        <a href="#">WORK</a>
        <a href="#">PRICING</a>
        <a href="#">SERVICES</a>
        <a href="#">BLOG</a>
        <a href="#">FEATURES</a>
        <a href="#">CONTACT</a>
      </nav>
    </header>

    <a class="slider-arrow slider-prev" href="#" aria-label="Previous slide">
      <svg width="14" height="20" viewBox="0 0 14 20"><path d="M10 3 L3 10 L10 17" fill="none" stroke="#fff" stroke-width="2"/></svg>
    </a>
    <a class="slider-arrow slider-next" href="#" aria-label="Next slide">
      <svg width="14" height="20" viewBox="0 0 14 20"><path d="M4 3 L11 10 L4 17" fill="none" stroke="#fff" stroke-width="2"/></svg>
    </a>

    <section class="hero-copy">
      <h1 class="hero-title">TALENTED TEAM OF<br>DEVELOPERS</h1>
      <p class="hero-text">We build responsive web sites and business intelligence platforms for small and medium businesses, turning scattered data into clear answers and fast, reliable tools your team can use every day.</p>
    </section>

    <div class="hero-actions">
      <a class="btn btn-outline" href="#">LEARN MORE</a>
      <a class="btn btn-primary" href="#">DOWNLOAD</a>
    </div>
  </main>
</body>
</html>
```